Business Card Design For Office Furniture Clearance Company

Kestrel Office Clearance - our company name pretty much explains what we do, we clear offices for high end clients, mainly plc's and large international companies.

We require a nice looking business card that displays professionalism but without being too serious.

It would be nice to see just a little more than a conventional boring business card, make sure you add some flare.

Industry/Entity Type

Office Furniture

Contact Information for Business Card

CARD 1

Mark Holloway
Director
mark@kestrelofficeclearance.co.uk
m: 07700 153928

t: 01632 960418
www.kestrelofficeclearance.co.uk

Kestrel Office Clearance
Unit K4 B
2-8 Fenwick Lane
Ashcombe
Harrowden Vale
ZZ9 4QT

tidy office clearances… handled start to finish.

CARD 2

Peter Radford
Director
peter@kestrelofficeclearance.co.uk
m: 07700 382615

t: 01632 960418

Kestrel Office Clearance
Unit K4 B
2-8 Fenwick Lane
Ashcombe
Harrowden Vale
ZZ9 4QT

Font styles to use
Sans Serif

Requirements
Must have
• A white background - as we have a blue logo.
Nice to have
• Nice use of the logo - play around with this and dissect it.

```html
<!DOCTYPE html>
<html lang="en">
<head>
<meta charset="utf-8">
<title>Kestrel Office Clearance – Business Card</title>
<link rel="stylesheet" href="https://fonts.googleapis.com/css2?family=Open+Sans:ital,wght@0,400;0,600;0,700;1,400&display=swap">
<style>
  :root {
    --brand-blue: #1277c0;
    --brand-blue-deep: #0a6aae;
    --brand-blue-light: #4aa3dc;
    --ink-grey: #555b62;
    --rule-grey: #d9dde1;
    --paper: #ffffff;
    --backdrop: #eceef0;
  }
  * { box-sizing: border-box; margin: 0; padding: 0; }
  html, body {
    width: 1200px; height: 950px; overflow: hidden;
    background: var(--backdrop);
    font-family: "Open Sans", sans-serif;
  }
  .sheet {
    position: relative; width: 1200px; height: 950px;
    display: flex; flex-direction: column; align-items: center; justify-content: center; gap: 40px;
  }
  .card {
    position: relative; width: 640px; height: 366px;
    box-shadow: 0 6px 18px rgba(0,0,0,.12);
  }
  .card-frame {
    position: absolute; inset: 12px; border: 1.5px solid var(--brand-blue);
  }

  /* Front */
  .card-front { background: var(--paper); }
  .brand-block {
    position: absolute; left: 40px; top: 0; bottom: 0; width: 230px;
    display: flex; flex-direction: column; align-items: center; justify-content: center; gap: 18px;
  }
  .brand-dot {
    width: 150px; height: 150px; border-radius: 50%;
    background: linear-gradient(135deg, var(--brand-blue-light), var(--brand-blue-deep));
  }
  .brand-name {
    color: var(--brand-blue); font-weight: 600; font-size: 17px; line-height: 1.25; text-align: center;
  }
  .details {
    position: absolute; left: 300px; right: 36px; top: 52px;
    color: var(--ink-grey); font-size: 13.5px; line-height: 1.45;
  }
  .person-name { color: var(--brand-blue); font-weight: 600; font-size: 24px; line-height: 1.1; }
  .person-role { font-size: 14px; margin-bottom: 10px; }
  .company-name { color: var(--brand-blue); font-weight: 700; font-size: 14.5px; }
  .details-rule { border: 0; border-top: 1px solid var(--rule-grey); margin: 16px 0 14px -40px; }
  .contact-list { list-style: none; }
  .contact-list li { display: flex; align-items: center; gap: 9px; height: 22px; }
  .contact-list svg { width: 14px; height: 14px; flex: none; fill: var(--brand-blue); }

  /* Back */
  .card-back { background: var(--brand-blue); }
  .card-back .card-frame { border-color: rgba(255,255,255,.9); border-width: 1px; }
  .back-brand {
    position: absolute; left: 0; right: 0; top: 108px;
    display: flex; align-items: center; justify-content: center; gap: 18px;
  }
  .back-dot { width: 110px; height: 110px; border-radius: 50%; background: var(--paper); }
  .back-name { color: var(--paper); font-weight: 600; font-size: 20px; line-height: 1.25; }
  .tagline {
    position: absolute; left: 0; right: 0; bottom: 34px; text-align: center;
    color: var(--paper); font-style: italic; font-size: 15px; letter-spacing: .2px;
  }
</style>
</head>
<body>
<main class="sheet">

  <section class="card card-front" aria-label="Business card front">
    <div class="card-frame"></div>

    <div class="brand-block">
      <div class="brand-dot"></div>
      <div class="brand-name">Kestrel<br>Office Clearance</div>
    </div>

    <div class="details">
      <div class="person-name">Mark Holloway</div>
      <div class="person-role">Director</div>
      <div class="company-name">Kestrel Office Clearance</div>
      <div class="address">Unit K4 B, 2-8 Fenwick Lane</div>
      <div class="address">Ashcombe, Harrowden Vale, ZZ9 4QT</div>
      <hr class="details-rule">
      <ul class="contact-list">
        <li>
          <svg viewBox="0 0 16 16" aria-hidden="true"><path d="M3.6 1.2l2.2 2.6-1.3 1.9c.9 2 2.6 3.7 4.6 4.6l1.9-1.3 2.6 2.2-1.4 2.2C7.2 13.3 2.7 8.8 1.4 3.2z"/></svg>
          <span>01632 960418</span>
        </li>
        <li>
          <svg viewBox="0 0 16 16" aria-hidden="true"><path d="M4.5 1h7A1.5 1.5 0 0 1 13 2.5v11a1.5 1.5 0 0 1-1.5 1.5h-7A1.5 1.5 0 0 1 3 13.5v-11A1.5 1.5 0 0 1 4.5 1zm.5 2v9h6V3zm3 9.8a.8.8 0 1 0 0 .01z"/></svg>
          <span>07700 153928</span>
        </li>
        <li>
          <svg viewBox="0 0 16 16" aria-hidden="true"><path d="M1 3.5h14v9H1zm1.4 1.2L8 8.8l5.6-4.1z"/></svg>
          <span>mark@kestrelofficeclearance.co.uk</span>
        </li>
        <li>
          <svg viewBox="0 0 16 16" aria-hidden="true"><path d="M8 1a7 7 0 1 0 0 14A7 7 0 0 0 8 1zm0 1.4c.8.9 1.4 2.2 1.6 3.6H6.4C6.6 4.6 7.2 3.3 8 2.4zM6.4 7.4h3.2c-.1 2-.7 3.6-1.6 4.7-.9-1.1-1.5-2.7-1.6-4.7zM2.5 7.4h2.5c.1 1.6.5 3.1 1.2 4.2A5.6 5.6 0 0 1 2.5 7.4zm8.5 0h2.5a5.6 5.6 0 0 1-3.7 4.2c.7-1.1 1.1-2.6 1.2-4.2zM2.5 6a5.6 5.6 0 0 1 3.7-3.6C5.5 3.4 5.1 4.6 5 6zm8.5 0c-.1-1.4-.5-2.6-1.2-3.6A5.6 5.6 0 0 1 13.5 6z"/></svg>
          <span>www.kestrelofficeclearance.co.uk</span>
        </li>
      </ul>
    </div>
  </section>

  <section class="card card-back" aria-label="Business card back">
    <div class="card-frame"></div>
    <div class="back-brand">
      <div class="back-dot"></div>
      <div class="back-name">Kestrel<br>Office Clearance</div>
    </div>
    <p class="tagline">tidy office clearances… handled start to finish.</p>
  </section>

</main>
</body>
</html>
```